Judicial election website to attract voters

I need a simple one-page web design for a judicial election. I'm going to put up one picture, maybe two. The picture I have needs a little touch-up (whiten teeth for example). I have 3 paragraphs of text. I'd like a "Donate" button that can link to a CoinDrift account. I'd also like a little background design, like the Constitution or something like that. There's a couple other little things but that's the bulk of it.

Target Market(s)

Involved voters and some media

Industry/Entity Type

Legal

Number of Pages Required

1 page

Font styles to use
Sans Serif

Requirements
Must have
• My picture, text, donate button
• Phrase "Remember to vote August 30, 2016!"
Nice to have
• Perhaps a second photo, maybe a short 30 second video of me talking directly to the voters, cool background: Constitution, something judgey.
Should not have
• Not sure ... profanity, I guess.

```html
<!DOCTYPE html>
<html lang="en">
<head>
<meta charset="utf-8">
<title>Delphine for Judge</title>
<link href="https://fonts.googleapis.com/css2?family=Bree+Serif&family=Raleway:wght@400;500;600&family=Open+Sans:wght@400;600&display=swap" rel="stylesheet">
<style>
  :root{
    --hero-dark:#3a2a22;
    --hero-mid:#7a5a40;
    --hero-warm:#b08860;
    --white:#ffffff;
    --brand-blue:#2a5ba3;
    --btn-blue-top:#3a6fb8;
    --btn-blue-bottom:#1f4f96;
    --body-grey:#7a7a7a;
    --heading-grey:#3a3a3a;
    --photo-bg:#e6e4e4;
    --video-bg-top:#e9ebee;
    --video-bg-bottom:#efe7de;
    --orange-top:#ffc21a;
    --orange-bottom:#f59c00;
    --footer-blue:#163e8c;
    --footer-text:#dfe7f5;
  }
  *{margin:0;padding:0;box-sizing:border-box}
  html,body{width:914px;height:1200px;overflow:hidden;background:var(--white)}
  body{position:relative;font-family:"Raleway",sans-serif}

  .hero{position:absolute;left:0;top:0;width:914px;height:453px;overflow:hidden}
  .hero-image{position:absolute;inset:0;background:
      linear-gradient(180deg,rgba(30,20,18,.55) 0%,rgba(40,28,22,.25) 45%,rgba(60,40,25,.15) 100%),
      linear-gradient(160deg,var(--hero-dark) 0%,var(--hero-mid) 45%,var(--hero-warm) 80%,#d2b48a 100%)}
  .logo{position:absolute;left:118px;top:20px;font-family:"Bree Serif",serif;font-size:31px;color:var(--white)}
  .main-nav{position:absolute;top:38px;left:373px;display:flex;gap:0}
  .main-nav a{position:absolute;font-size:12px;font-weight:500;color:var(--white);text-decoration:none;white-space:nowrap;font-family:"Open Sans",sans-serif}
  .main-nav .active::after{content:"";position:absolute;left:-4px;right:-4px;top:23px;height:2px;background:var(--white)}
  .hero-title{position:absolute;left:0;width:914px;top:196px;text-align:center;color:var(--white);font-size:32px;font-weight:500;letter-spacing:.3px}
  .hero-sub{position:absolute;left:0;width:914px;top:240px;text-align:center;color:var(--white);font-size:21px;font-weight:400}
  .slider-dots{position:absolute;top:424px;left:427px;display:flex;gap:3px}
  .slider-dots span{width:13px;height:13px;border-radius:50%;background:var(--white)}
  .slider-dots span.current{background:transparent;border:1.5px solid var(--white)}

  .about-title{position:absolute;top:492px;left:0;width:914px;text-align:center;font-size:22px;font-weight:500;color:var(--brand-blue);letter-spacing:.5px}
  .portrait{position:absolute;left:114px;top:550px;width:228px;height:235px;background:linear-gradient(180deg,#ecebeb,#d9c7bb 70%,#d98c73)}
  .portrait::after{content:"";position:absolute;left:7px;top:9px;right:8px;bottom:10px;border:2px solid var(--white)}
  .about-text{position:absolute;left:361px;top:547px;width:458px;font-family:"Open Sans",sans-serif;font-size:9.2px;line-height:16.2px;color:var(--body-grey)}
  .about-text p+p{margin-top:13px}
  .about-text p.tight{margin-top:0}
  .btn{position:absolute;display:flex;align-items:center;justify-content:center;width:87px;height:26px;border-radius:2px;color:var(--white);font-size:10px;font-weight:600;text-decoration:none;font-family:"Open Sans",sans-serif}
  .btn-read{left:359px;top:753px;background:linear-gradient(var(--btn-blue-top),var(--btn-blue-bottom))}

  .video-section{position:absolute;left:0;top:843px;width:914px;height:259px;background:linear-gradient(90deg,var(--video-bg-top),#ecebe9 50%,var(--video-bg-bottom))}
  .video-title{position:absolute;left:118px;top:42px;font-size:22px;font-weight:400;color:var(--heading-grey)}
  .video-text{position:absolute;left:121px;top:81px;width:400px;font-family:"Open Sans",sans-serif;font-size:9.2px;line-height:16.2px;color:#666}
  .video-text p+p{margin-top:10px}
  .btn-donate{left:122px;top:185px;background:linear-gradient(var(--orange-top),var(--orange-bottom))}
  .video-frame{position:absolute;left:536px;top:46px;width:278px;height:176px;background:var(--white);padding:5px;box-shadow:0 0 3px rgba(0,0,0,.15)}
  .video-still{position:relative;width:100%;height:100%;background:linear-gradient(150deg,#243a5c 0%,#3a4a66 30%,#c89a52 55%,#e2c27e 75%,#8a5a3a 100%)}
  .play{position:absolute;left:116px;top:70px;width:34px;height:34px;border-radius:50%;background:var(--white)}
  .play::after{content:"";position:absolute;left:13px;top:9px;border-left:11px solid #111;border-top:8px solid transparent;border-bottom:8px solid transparent}
  .controls{position:absolute;left:0;right:0;bottom:0;height:20px;background:#1a1a1a}

  .site-footer{position:absolute;left:0;top:1103px;width:914px;height:97px;background:var(--footer-blue)}
  .footer-nav{position:absolute;top:25px;left:0;width:914px;display:flex;justify-content:center;gap:31px}
  .footer-nav a{font-family:"Open Sans",sans-serif;font-size:11px;color:var(--footer-text);text-decoration:none}
  .copyright{position:absolute;top:45px;left:0;width:914px;text-align:center;font-family:"Open Sans",sans-serif;font-size:8.5px;color:#b9c6e2}
  .social{position:absolute;top:67px;left:0;width:914px;display:flex;justify-content:center;gap:12px}
  .social a{display:flex;align-items:center;gap:4px;font-family:"Open Sans",sans-serif;font-size:9px;color:var(--footer-text);text-decoration:none}
  .social a::before{content:"";width:18px;height:18px;border-radius:50%;border:1.5px solid var(--footer-text)}
</style>
</head>
<body>
  <header class="hero">
    <div class="hero-image" role="img" aria-label="Photo of a quill, candle and the Constitution on an American flag"></div>
    <div class="logo">Delphine</div>
    <nav class="main-nav">
      <a class="active" href="#" style="left:0">HOME</a>
      <a href="#" style="left:69px">ABOUT</a>
      <a href="#" style="left:143px">VIDEO</a>
      <a href="#" style="left:212px">DONATE</a>
      <a href="#" style="left:293px">BLOG</a>
      <a href="#" style="left:359px">CONTACT</a>
    </nav>
    <h1 class="hero-title">Remember to vote August 30, 2016</h1>
    <p class="hero-sub">Praesent sit amet est dictum dolor</p>
    <div class="slider-dots"><span class="current"></span><span></span><span></span><span></span></div>
  </header>

  <section class="about">
    <h2 class="about-title">EXPERIENCED . DEDICATED . RESPECTED</h2>
    <div class="portrait" role="img" aria-label="Portrait photo of the candidate"></div>
    <div class="about-text">
      <p>Delphine was born and raised in Bayview, the daughter of an air-conditioning repairman who later opened his own successful business. As the first in her family to go to college, her parents could not have been more proud as she finished her degree at Gulfshore University, then continued on to Palmetto College of Law where she graduated with honors.</p>
      <p>Dedicating her life to public service in the region, she has spent the last 18 years as a prosecutor fighting for victims of child abuse and sexual abuse in Cedar and Willow counties. She participates in local charities such as the Harvest Table Pantry and the Open Page Reading Circle.</p>
      <p class="tight">Delphine shares her knowledge and experience freely, often mentoring the other young prosecutors and lecturing on jury selection and trial strategies. She is also committed to ensuring ethical behavior in the profession of law. In law school, she won an award for ethics and professionalism but since then she also served as Chair of a State Bar Grievance Committee, which handles complaints</p>
    </div>
    <a class="btn btn-read" href="#">READ MORE</a>
  </section>

  <section class="video-section">
    <h2 class="video-title">Watch Latest Video</h2>
    <div class="video-text">
      <p>The cornerstone of Delphine's candidacy for judge is her experience in the courtroom. Nobody knows how to run an efficient courtroom better than an attorney who has litigated a hundred felony jury trials and argued more pretrial motions than can be counted.</p>
      <p>But even a judge with all the right knowledge and experience cannot excel without the correct temperament. Ask any attorney or judge who has worked with Delphine.</p>
    </div>
    <a class="btn btn-donate" href="#">DONATE</a>
    <div class="video-frame">
      <div class="video-still" role="img" aria-label="Video still of the Constitution on a flag">
        <span class="play"></span>
        <div class="controls">
          <svg width="268" height="20" viewBox="0 0 268 20">
            <polygon points="9,6 9,14 16,10" fill="#fff"/>
            <rect x="22" y="9" width="225" height="3" rx="1.5" fill="#ddd"/>
            <rect x="22" y="9" width="90" height="3" rx="1.5" fill="#3a78d0"/>
            <polygon points="252,8 255,8 258,5 258,15 255,12 252,12" fill="#fff"/>
          </svg>
        </div>
      </div>
    </div>
  </section>

  <footer class="site-footer">
    <nav class="footer-nav">
      <a href="#">HOME</a><a href="#">ABOUT</a><a href="#">VIDEO</a><a href="#">DONATE</a><a href="#">BLOG</a><a href="#">CONTACT</a>
    </nav>
    <p class="copyright">© 2016 Company Name&nbsp; All right reserved</p>
    <div class="social">
      <a href="#">Murmur</a><a href="#">Gatherly</a><a href="#">Linkfold</a><a href="#">Orbitly</a>
    </div>
  </footer>
</body>
</html>
```